Bramblewick Forage Business Cards

I need a business card with my logo, number, Facebook account, and some information about what I am selling. Green card with logo on the front. 555-214-8392 phone number, @bramblewickforage Facebook, •Orchardgrass Hay •Alfalfa Hay •Mixed Grass Hay , and “Premium Quality Hay” all written on the back.

Target Market(s)

Hay

Contact Information for Business Card

Phone number, Facebook, different types of hay.

Colors
00AB8E
00BBA5
67D7C9
C6EFE9
E9F9F6

```html
<!DOCTYPE html>
<html lang="en">
<head>
<meta charset="utf-8">
<title>Bramblewick Forage Business Cards</title>
<link rel="stylesheet" href="https://fonts.googleapis.com/css2?family=Arimo:wght@400;700&family=Yellowtail&display=swap">
<style>
  :root {
    --backdrop: #ececec;
    --card-dark: #2b2b2d;
    --card-edge: #0a9a4a;
    --green-light: #05b35c;
    --green-mid: #00a04c;
    --green-deep: #008a3f;
    --brand-green: #12a24f;
    --ink-white: #ffffff;
    --ink-soft: #e4e4e4;
    --rule: #8a8a8a;
  }
  * { box-sizing: border-box; margin: 0; padding: 0; }
  html, body {
    width: 1200px; height: 801px; overflow: hidden;
    background: var(--backdrop);
    font-family: "Arimo", Arial, sans-serif;
  }
  .sheet {
    position: relative; width: 1200px; height: 801px;
    display: flex; align-items: center; justify-content: center; gap: 60px;
  }
  .card {
    position: relative; width: 530px; height: 303px;
    border-bottom: 4px solid var(--card-edge);
    box-shadow: 0 10px 24px rgba(0,0,0,0.22);
    overflow: hidden;
  }
  /* Contact side */
  .card--contact { background: var(--card-dark); color: var(--ink-white); }
  .card--contact .brand-name {
    position: absolute; top: 58px; left: 0; right: 0; text-align: center;
    font-weight: 700; font-size: 30px; color: var(--ink-white);
  }
  .holder {
    position: absolute; left: 36px; top: 168px;
  }
  .holder__name {
    font-family: "Yellowtail", cursive; font-size: 36px; line-height: 1;
    color: var(--brand-green);
  }
  .holder__role { font-size: 15px; color: var(--ink-soft); margin-top: 4px; }
  .divider {
    position: absolute; left: 30px; right: 30px; top: 232px;
    height: 1px; background: var(--rule);
  }
  .contact-line {
    position: absolute; top: 246px; display: flex; align-items: center; gap: 8px;
    font-size: 17px; color: var(--ink-soft);
  }
  .contact-line--phone { left: 36px; }
  .contact-line--social { right: 36px; }
  .contact-line svg { display: block; }
  .social-square {
    width: 16px; height: 16px; border-radius: 3px; background: var(--brand-green);
  }
  /* Product side */
  .card--products {
    background: radial-gradient(ellipse at 55% 40%, var(--green-light) 0%, var(--green-mid) 55%, var(--green-deep) 100%);
    color: var(--ink-white);
  }
  .card--products .brand-name {
    position: absolute; top: 104px; left: 0; right: 0; text-align: center;
    font-weight: 700; font-size: 34px; color: var(--ink-white);
  }
  .product-list {
    position: absolute; left: 0; right: 0; bottom: 48px;
    display: flex; justify-content: center; flex-wrap: nowrap; gap: 10px;
    list-style: none; font-weight: 700; font-size: 13px; color: var(--ink-soft);
  }
  .product-list li::before { content: "•"; margin-right: 5px; }
</style>
</head>
<body>
<main class="sheet">
  <section class="card card--contact" aria-label="Card front with contact details">
    <p class="brand-name">Bramblewick Forage</p>
    <div class="holder">
      <p class="holder__name">Elias Fernwood</p>
      <p class="holder__role">Manager</p>
    </div>
    <div class="divider"></div>
    <p class="contact-line contact-line--phone">
      <svg width="16" height="16" viewBox="0 0 24 24" aria-hidden="true">
        <path fill="#12a24f" d="M6.6 10.8a15.1 15.1 0 0 0 6.6 6.6l2.2-2.2a1 1 0 0 1 1-.25 11.4 11.4 0 0 0 3.6.6 1 1 0 0 1 1 1V20a1 1 0 0 1-1 1A17 17 0 0 1 3 4a1 1 0 0 1 1-1h3.5a1 1 0 0 1 1 1c0 1.25.2 2.45.6 3.6a1 1 0 0 1-.25 1z"/>
      </svg>
      555-214-8392
    </p>
    <p class="contact-line contact-line--social">
      <span class="social-square" aria-hidden="true"></span>
      @bramblewickforage
    </p>
  </section>

  <section class="card card--products" aria-label="Card back with products">
    <p class="brand-name">Bramblewick Forage</p>
    <ul class="product-list">
      <li>Orchardgrass Hay</li>
      <li>Alfalfa Hay</li>
      <li>Mixed Grass Hay</li>
      <li>Premium Quality Hay</li>
    </ul>
  </section>
</main>
</body>
</html>
```